SkyvornQ Business Cards and Stationary Design

Need a design for our business cards and stationary. I want to carry on the theme of the logo. I want the business cards to have a design on the back. I would like the business cards and the stationary to carry the same theme, design scheme, and branding

Target Market(s)

Airlines and Maintenance Facilities

Industry/Entity Type

Aviation

Contact Information for Business Card

Name
Position Title
Address: 4827 Trellis Hollow Road, Fort Pierce, Florida, 34951
Office Number
Mobile Number
Email
Website

Font styles to use
Serif
Sans Serif

Colors

Designer to choose colors to be used in the design.

```html
<!DOCTYPE html>
<html lang="en">
<head>
<meta charset="utf-8">
<title>SkyvornQ Business Card</title>
<link href="https://fonts.googleapis.com/css2?family=Open+Sans:wght@400;600;700&display=swap" rel="stylesheet">
<style>
  :root {
    --backdrop: #9a9a9a;
    --paper: #ffffff;
    --navy: #0b2850;
    --brand-blue: #1a7fc8;
    --ink: #1d1d1d;
    --rule-light: #d8d8d8;
    --rule-dark: #3d5778;
  }
  * { margin: 0; padding: 0; box-sizing: border-box; }
  html, body { width: 1200px; height: 900px; overflow: hidden; }
  body {
    position: relative;
    background: var(--backdrop);
    font-family: "Open Sans", Arial, sans-serif;
    color: var(--ink);
  }
  .card {
    position: absolute;
    width: 478px;
    height: 294px;
    box-shadow: 2px 3px 5px rgba(0,0,0,0.35);
  }
  .card-front {
    left: 120px; top: 275px;
    background: var(--paper);
    border-radius: 0 50px 0 50px;
  }
  .card-back {
    left: 606px; top: 274px;
    background: var(--navy);
    border-radius: 50px 0 50px 0;
  }
  .brand-ring {
    position: absolute;
    border-radius: 50%;
  }
  .card-front .brand-ring {
    left: 298px; top: 53px; width: 76px; height: 76px;
    border: 5px solid var(--brand-blue);
  }
  .card-back .brand-ring {
    left: 196px; top: 76px; width: 86px; height: 86px;
    border: 5px solid var(--paper);
  }
  .brand-name {
    position: absolute;
    font-weight: 700;
    letter-spacing: 3px;
    line-height: 1;
  }
  .card-front .brand-name {
    right: 34px; top: 136px;
    font-size: 25px;
    color: var(--navy);
  }
  .card-back .brand-name {
    left: 0; width: 100%; top: 179px;
    text-align: center;
    font-size: 29px;
    color: var(--paper);
  }
  .person-name {
    position: absolute;
    left: 30px; top: 161px;
    font-size: 16px; font-weight: 700;
    color: var(--navy);
    letter-spacing: 0.3px;
  }
  .person-title {
    position: absolute;
    left: 29px; top: 180px;
    font-size: 12.5px;
  }
  .front-rule {
    position: absolute;
    left: 148px; top: 190px; width: 296px;
    border-top: 1px solid var(--rule-light);
  }
  .address {
    position: absolute;
    left: 31px; top: 235px;
    font-size: 12.5px; line-height: 17.5px;
  }
  .contact-list {
    position: absolute;
    right: 33px; top: 200px;
    list-style: none;
    font-size: 12.5px; line-height: 17.5px;
    text-align: right;
  }
  .contact-list li { display: flex; justify-content: flex-end; align-items: center; gap: 2px; }
  .contact-list svg { width: 11px; height: 11px; fill: var(--navy); }
  .back-rule {
    position: absolute;
    left: 97px; top: 231px; width: 283px;
    border-top: 1px solid var(--rule-dark);
  }
  .back-web {
    position: absolute;
    left: 0; width: 100%; top: 248px;
    text-align: center;
    font-size: 12.5px; font-weight: 600;
    letter-spacing: 1px;
    color: var(--paper);
  }
</style>
</head>
<body>
  <section class="card card-front">
    <span class="brand-ring"></span>
    <div class="brand-name">SKYVORNQ</div>
    <div class="person-name">DORIAN VEXLEY</div>
    <div class="person-title">Managing Director</div>
    <div class="front-rule"></div>
    <ul class="contact-list">
      <li>044-987 654 321<svg viewBox="0 0 12 12"><path d="M1 4c0-2 2-3 5-3s5 1 5 3l-2 1-1-2H4L3 5 1 4zm2 2h6l1 5H2l1-5zm3 1a1.5 1.5 0 100 3 1.5 1.5 0 000-3z"/></svg></li>
      <li>044-987 654 321<svg viewBox="0 0 12 12"><path d="M3 0h6v12H3V0zm1 1.5v8h4v-8H4zm2 8.8a.7.7 0 100 1.4.7.7 0 000-1.4z"/></svg></li>
      <li>info@skyvornq.com<svg viewBox="0 0 12 12"><path d="M0 2h12v8H0V2zm1 1v.3l5 3.2 5-3.2V3H1z"/></svg></li>
      <li>www.skyvornq.com<svg viewBox="0 0 12 12"><circle cx="6" cy="6" r="5.5"/></svg></li>
    </ul>
    <address class="address" style="font-style:normal">
      4827 Trellis Hollow Road<br>Fort Pierce, Florida, 34951
    </address>
  </section>

  <section class="card card-back">
    <span class="brand-ring"></span>
    <div class="brand-name">SKYVORNQ</div>
    <div class="back-rule"></div>
    <div class="back-web">www.skyvornq.com</div>
  </section>
</body>
</html>
```